Business Cards for new orthopaedic surgery practice

My husband and I are starting our own orthopaedic surgery practice. We are looking for a business card that is uniform, but one will have my name/title and the other will have his. You can just create one design with my name on it for now. But when I choose your design as the winning design I will ask that you add another copy with his name/title.

We are looking for classy, simple, elite all in one. We like dark blues/a little gold/yellow. Something that goes with our logo. We want our logo incorporated. Here is all the info you need:
Business name: RV Bone & Vitality Center
Location: 38517 North Willowmere Ave
Maple Hollow, FL 33990
Phone: 954-218-4063
Fax: 954-582-7341
Email: info@myrvbonecare.example

Names: Lydia Vance, M.D.
Board Certified Hand and Upper Extremity Surgeon

Ebo Dansu, M.D.
Board Certified Hip & Knee Replacement/General Orthopaedic Surgeon

Can decide what you want to put on the back. Maybe a slogan:
Rooted in Care. Focused on You

I am just going to upload our logo. The only thing is if we select you as the winning design, the location, and phone numbers may change. We will need your help to update that once fully solidified.

Industry/Entity Type

Medical

Contact Information for Business Card

Colors
0054AA
0677BA
7BADD7
CADEEF
E8F1F8
0094D4
00A9DD
6FCCEA
C7EBF8
E9F6FB

Requirements
Must have
• class, appeal,
Should not have
• We want to air on the side of masculine if we are looking at masculine vs. feminine feel. But we still want it classy, sophisticated, and something we will love

```html
<!DOCTYPE html>
<html lang="en">
<head>
<meta charset="utf-8">
<title>RV Bone &amp; Vitality Center – Business Card</title>
<link rel="stylesheet" href="https://fonts.googleapis.com/css2?family=Montserrat:wght@500;600;700&family=Arimo:wght@400&display=swap">
<style>
  :root {
    --backdrop: #2b2b2b;
    --navy: #1b2a52;
    --gold: #c29a4e;
    --paper: #ffffff;
    --ink: #1e1e1e;
  }
  * { box-sizing: border-box; margin: 0; padding: 0; }
  html, body { width: 1200px; height: 800px; overflow: hidden; }
  body {
    background: var(--backdrop);
    display: flex;
    align-items: center;
    justify-content: center;
    gap: 44px;
    font-family: "Arimo", Arial, sans-serif;
  }
  .card {
    position: relative;
    width: 520px;
    height: 298px;
    border-radius: 16px;
    overflow: hidden;
  }

  /* Back side */
  .card-back {
    background: var(--navy);
    display: flex;
    align-items: center;
    justify-content: center;
  }
  .back-seal {
    width: 190px;
    height: 190px;
    border: 2px solid var(--paper);
    border-radius: 50%;
    display: flex;
    align-items: center;
    justify-content: center;
    text-align: center;
  }
  .back-seal .brand-name {
    font-family: "Montserrat", sans-serif;
    font-weight: 600;
    font-size: 17px;
    line-height: 1.35;
    letter-spacing: 2px;
    text-transform: uppercase;
    color: var(--paper);
    width: 150px;
  }

  /* Front side */
  .card-front { background: var(--paper); }
  .front-decoration {
    position: absolute;
    left: -40px;
    bottom: -70px;
    width: 250px;
    height: 250px;
    border-radius: 50%;
    background: var(--navy);
    display: flex;
    align-items: flex-start;
    justify-content: center;
    padding-top: 62px;
  }
  .front-decoration .brand-name {
    font-family: "Montserrat", sans-serif;
    font-weight: 700;
    font-size: 30px;
    line-height: 1.05;
    color: var(--paper);
    width: 150px;
    text-align: center;
  }
  .front-details {
    position: absolute;
    left: 232px;
    top: 40px;
    width: 200px;
  }
  .company {
    font-family: "Montserrat", sans-serif;
    font-weight: 600;
    font-size: 16px;
    line-height: 1.2;
    color: var(--gold);
    margin-bottom: 12px;
    white-space: nowrap;
  }
  .person {
    font-family: "Montserrat", sans-serif;
    font-weight: 700;
    font-size: 17px;
    color: var(--navy);
    letter-spacing: 0.3px;
    white-space: nowrap;
  }
  .person .credential { color: var(--gold); font-weight: 600; }
  .role {
    font-size: 12.5px;
    line-height: 1.3;
    color: var(--ink);
    margin-top: 3px;
    margin-bottom: 16px;
  }
  .contact-list { list-style: none; }
  .contact-list li {
    display: flex;
    align-items: flex-start;
    gap: 8px;
    font-size: 12.5px;
    line-height: 1.3;
    color: var(--ink);
    margin-bottom: 3px;
    white-space: nowrap;
  }
  .contact-list svg { flex: none; width: 11px; height: 11px; margin-top: 2px; fill: var(--gold); }
  .corner-seal {
    position: absolute;
    right: 16px;
    top: 112px;
    width: 62px;
    height: 62px;
    border: 1.5px solid var(--gold);
    border-radius: 50%;
    display: flex;
    align-items: center;
    justify-content: center;
    text-align: center;
  }
  .corner-seal .brand-name {
    font-family: "Montserrat", sans-serif;
    font-weight: 700;
    font-size: 7px;
    line-height: 1.2;
    color: var(--navy);
    width: 48px;
  }
</style>
</head>
<body>
  <section class="card card-back" aria-label="Card back">
    <div class="back-seal">
      <span class="brand-name">RV Bone &amp; Vitality Center</span>
    </div>
  </section>

  <section class="card card-front" aria-label="Card front">
    <div class="front-decoration">
      <span class="brand-name">RV Bone &amp; Vitality</span>
    </div>

    <div class="front-details">
      <p class="company">RV Bone &amp; Vitality Center</p>
      <p class="person">LYDIA VANCE, <span class="credential">M.D.</span></p>
      <p class="role">Board Certified Hand and<br>Upper Extremity Surgeon</p>
      <ul class="contact-list">
        <li>
          <svg viewBox="0 0 12 12" aria-hidden="true"><path d="M3 0h6a1 1 0 0 1 1 1v10a1 1 0 0 1-1 1H3a1 1 0 0 1-1-1V1a1 1 0 0 1 1-1zm0 1.5v8h6v-8z"/></svg>
          954-218-4063
        </li>
        <li>
          <svg viewBox="0 0 12 12" aria-hidden="true"><path d="M3 0h6v3H3zM1 4h10a1 1 0 0 1 1 1v4H10v3H2V9H0V5a1 1 0 0 1 1-1zm2 4v3h6V8z"/></svg>
          954-582-7341
        </li>
        <li>
          <svg viewBox="0 0 12 12" aria-hidden="true"><path d="M0 5 12 0 7 12 5.5 7z"/></svg>
          info@myrvbonecare.example
        </li>
        <li>
          <svg viewBox="0 0 12 12" aria-hidden="true"><path d="M6 0a4 4 0 0 1 4 4c0 3-4 8-4 8S2 7 2 4a4 4 0 0 1 4-4zm0 2.5A1.5 1.5 0 1 0 6 5.5 1.5 1.5 0 0 0 6 2.5z"/></svg>
          <span>38517 North Willowmere Ave<br>Maple Hollow, FL 33990</span>
        </li>
      </ul>
    </div>

    <div class="corner-seal">
      <span class="brand-name">RV Bone &amp; Vitality Center</span>
    </div>
  </section>
</body>
</html>
```